Modern card design needed for building development company

We are looking for a sharp modern new look for our business cards.
We are a New Zealand based company called TKR Ventures NZ LTD that specialises in subdividing large sections, housing and commercial buildings.
We have attached a photo of the current logo and would like to see it improved somehow as it looks a bit dated.
We are open to any colours.

Target Market(s)

Investors, Property buyers

Industry/Entity Type

Investment

Contact Information for Business Card

TKR VENTURES NZ LTD
www.tkrventuresnz.co.nz

Damon Whitcombe
Phone +64 21 938 104
Email dpwhitcombe@korumail.co.nz

Font styles to use
Serif
Sans Serif

Colors
0792cd
33a6d7
85cae6
6b449b
886aae
f04a50
ec1f27
f37122
f68d4d

Requirements
Must have
• Please try and make the logo more modern or if you have a similar one we would like to see it.

```html
<!DOCTYPE html>
<html lang="en">
<head>
<meta charset="UTF-8">
<title>TKR Ventures NZ LTD – Business Card</title>
<link href="https://fonts.googleapis.com/css2?family=Montserrat:wght@500;600;700&family=Work+Sans:wght@300;400&display=swap" rel="stylesheet">
<style>
  :root {
    --backdrop: #1c1c1d;
    --card: #161617;
    --card-edge: #202021;
    --ink: #ffffff;
    --ink-soft: #d6d6d6;
    --ink-muted: #a9a9a9;
  }
  * { margin: 0; padding: 0; box-sizing: border-box; }
  html, body {
    width: 1200px;
    height: 900px;
    overflow: hidden;
    background: var(--backdrop);
  }
  .canvas {
    position: relative;
    width: 1200px;
    height: 900px;
  }
  .card {
    position: absolute;
    left: 250px;
    width: 700px;
    height: 400px;
    background: linear-gradient(135deg, var(--card-edge) 0%, var(--card) 60%);
    box-shadow: 0 14px 30px rgba(0,0,0,0.55);
  }
  .card--front { top: 36px; }
  .card--back { top: 464px; }

  .front-name {
    position: absolute;
    inset: 0;
    display: flex;
    align-items: center;
    justify-content: center;
    font-family: "Montserrat", sans-serif;
    font-weight: 600;
    font-size: 30px;
    letter-spacing: 4px;
    color: var(--ink);
  }

  .brand {
    position: absolute;
    left: 60px;
    top: 0;
    height: 100%;
    width: 250px;
    display: flex;
    align-items: center;
    gap: 12px;
  }
  .brand-square {
    width: 16px;
    height: 16px;
    background: var(--ink);
    flex: none;
  }
  .brand-name {
    font-family: "Montserrat", sans-serif;
    font-weight: 600;
    font-size: 15px;
    letter-spacing: 2px;
    color: var(--ink);
    white-space: nowrap;
  }

  .divider {
    position: absolute;
    left: 345px;
    top: 90px;
    width: 2px;
    height: 220px;
    background: var(--ink);
  }

  .contact {
    position: absolute;
    left: 385px;
    top: 92px;
    font-family: "Work Sans", sans-serif;
    font-weight: 300;
    color: var(--ink-soft);
  }
  .person-name {
    font-family: "Montserrat", sans-serif;
    font-weight: 700;
    font-size: 24px;
    letter-spacing: 1.5px;
    color: var(--ink);
  }
  .person-role {
    font-size: 16px;
    color: var(--ink-muted);
    margin-top: 2px;
  }
  .address {
    font-size: 17px;
    line-height: 1.25;
    margin-top: 16px;
  }
  .contact-list {
    list-style: none;
    margin-top: 12px;
  }
  .contact-list li {
    display: flex;
    align-items: center;
    gap: 12px;
    font-size: 17px;
    line-height: 1.4;
  }
  .contact-icon {
    width: 12px;
    height: 12px;
    flex: none;
  }
</style>
</head>
<body>
<main class="canvas">
  <section class="card card--front" aria-label="Card front">
    <h1 class="front-name">TKR VENTURES NZ LTD</h1>
  </section>

  <section class="card card--back" aria-label="Card back">
    <div class="brand">
      <span class="brand-square"></span>
      <span class="brand-name">TKR VENTURES NZ LTD</span>
    </div>

    <div class="divider"></div>

    <div class="contact">
      <h2 class="person-name">DAMON WHITCOMBE</h2>
      <p class="person-role">Director</p>
      <p class="address">PO BOX 48215 Devonport<br>Auckland New Zealand</p>
      <ul class="contact-list">
        <li>
          <svg class="contact-icon" viewBox="0 0 12 12" aria-hidden="true">
            <path d="M2.5 1 L4.5 1 L5.2 3.4 L4 4.4 Q5 6.8 7.6 8 L8.6 6.8 L11 7.5 L11 9.5 Q10.5 11 9 11 Q1 10 1 2.8 Q1 1.4 2.5 1 Z" fill="none" stroke="#d6d6d6" stroke-width="1"/>
          </svg>
          <span>+64 21 938 104</span>
        </li>
        <li>
          <svg class="contact-icon" viewBox="0 0 12 12" aria-hidden="true">
            <rect x="0.75" y="2.25" width="10.5" height="7.5" fill="none" stroke="#d6d6d6" stroke-width="1"/>
            <path d="M0.75 2.5 L6 6.5 L11.25 2.5" fill="none" stroke="#d6d6d6" stroke-width="1"/>
          </svg>
          <span>dpwhitcombe@korumail.co.nz</span>
        </li>
        <li>
          <svg class="contact-icon" viewBox="0 0 12 12" aria-hidden="true">
            <circle cx="6" cy="6" r="5.2" fill="none" stroke="#d6d6d6" stroke-width="1"/>
            <ellipse cx="6" cy="6" rx="2.2" ry="5.2" fill="none" stroke="#d6d6d6" stroke-width="1"/>
            <path d="M0.8 6 H11.2 M1.6 3.4 H10.4 M1.6 8.6 H10.4" stroke="#d6d6d6" stroke-width="0.8"/>
          </svg>
          <span>www.tkrventuresnz.co.nz</span>
        </li>
      </ul>
    </div>
  </section>
</main>
</body>
</html>
```